Shine Fox Auto Care Business Card

2 side business card design for an auto detailing business

Target Market(s)

Auto detailing

Contact Information for Business Card

Things included

The business name “Shine Fox Auto Care”
Mark Dunrow
(403)271-6094
Merridale, Sk

Services offered - complete interior& exterior detail
- paint correction & protection
- ceramic coating
- trim restore
- auto carpet & seat cleaning

Requirements
Must have
• Colours that are in my logo

Services offered

My name Mark Dunrow
403-271-6094
Merridale, Sk

Not too sure in what order for these ?
Website. Shinefoxautocare.com
Instagram Shinefoxautocare
Email. Shinefoxautoac@mailvento.com

```html
<!DOCTYPE html>
<html lang="en">
<head>
<meta charset="utf-8">
<title>Shine Fox Auto Care – Business Card</title>
<link rel="stylesheet" href="https://fonts.googleapis.com/css2?family=Arimo:wght@400;700&family=Michroma&display=swap">
<style>
  :root {
    --stage: #2a2a2a;
    --card-dark: #000000;
    --card-light: #ffffff;
    --ink: #111111;
    --ink-soft: #1c1c1c;
    --red: #9b1010;
    --white: #ffffff;
    --divider: #c9c9c9;
  }
  * { box-sizing: border-box; margin: 0; padding: 0; }
  html, body { width: 1200px; height: 900px; overflow: hidden; }
  body {
    background: var(--stage);
    font-family: "Arimo", Arial, sans-serif;
    position: relative;
  }
  .card {
    position: absolute;
    left: 270px;
    width: 660px;
    height: 377px;
    box-shadow: 0 10px 30px rgba(0,0,0,.55);
  }
  .card--back { top: 45px; background: var(--card-dark); color: var(--white); }
  .card--front { top: 470px; background: var(--card-light); color: var(--ink); }

  /* brand lockup */
  .brand { text-align: center; }
  .brand__mark {
    width: 58px; height: 58px; border-radius: 50%;
    border: 7px solid currentColor;
    margin: 0 auto 14px;
  }
  .brand__name {
    font-family: "Arimo", Arial, sans-serif;
    font-weight: 700;
    font-size: 30px;
    letter-spacing: 2px;
    text-transform: uppercase;
    line-height: 1.1;
    white-space: nowrap;
  }

  /* back side */
  .card--back .brand { padding-top: 62px; }
  .card--back .brand__mark { border-color: var(--white); }
  .tagline {
    text-align: center;
    font-size: 14px;
    letter-spacing: .3px;
    margin-top: 26px;
  }
  .services {
    list-style: none;
    display: grid;
    grid-template-columns: auto auto;
    justify-content: center;
    column-gap: 40px;
    row-gap: 6px;
    margin-top: 26px;
    font-size: 16px;
  }
  .services li { display: flex; align-items: center; gap: 8px; }
  .services li::before {
    content: ""; width: 11px; height: 11px; border-radius: 50%;
    border: 1.5px solid var(--white);
  }

  /* front side */
  .front__logo {
    position: absolute; left: 0; top: 0; width: 330px; height: 100%;
    display: flex; align-items: center; justify-content: center;
  }
  .front__logo .brand__mark { border-color: var(--red); }
  .front__logo .brand__name { color: var(--ink); font-size: 21px; letter-spacing: 1.5px; }
  .front__divider {
    position: absolute; left: 330px; top: 40px; width: 1px; height: 297px;
    background: var(--divider);
  }
  .contact { position: absolute; left: 365px; top: 78px; }
  .contact__name {
    font-family: "Michroma", Arial, sans-serif;
    color: var(--red);
    font-size: 21px;
    letter-spacing: 1px;
    margin-bottom: 16px;
    font-weight: 400;
  }
  .contact__list { list-style: none; font-size: 16px; color: var(--ink-soft); }
  .contact__list li { display: flex; align-items: center; gap: 9px; margin-bottom: 9px; }
  .contact__list li.gap { margin-top: 12px; }
  .icon {
    width: 20px; height: 20px; border-radius: 50%;
    background: var(--red); flex: none;
    display: flex; align-items: center; justify-content: center;
  }
  .icon svg { width: 12px; height: 12px; }
  .accent { color: var(--red); }
</style>
</head>
<body>

<section class="card card--back">
  <div class="brand">
    <div class="brand__mark"></div>
    <div class="brand__name">Shine Fox Auto Care</div>
  </div>
  <p class="tagline">COMPLETE INTERIOR &amp; EXTERIOR DETAIL</p>
  <ul class="services">
    <li>Paint correction &amp; protection</li>
    <li>Ceramic coating</li>
    <li>Auto carpet &amp; seat cleaning</li>
    <li>Trim restore</li>
  </ul>
</section>

<section class="card card--front">
  <div class="front__logo">
    <div class="brand">
      <div class="brand__mark"></div>
      <div class="brand__name">Shine Fox Auto Care</div>
    </div>
  </div>
  <div class="front__divider"></div>
  <div class="contact">
    <h1 class="contact__name">MARK DUNROW</h1>
    <ul class="contact__list">
      <li><span class="icon"><svg viewBox="0 0 12 12"><path d="M2.5 1.5l2 2-1 1.2c.6 1.4 1.6 2.4 3 3l1.2-1 2 2-1.2 1.3C5.5 9.8 2.2 6.5 1.2 2.7z" fill="#fff"/></svg></span><span>(403)271-6094</span></li>
      <li><span class="icon"><svg viewBox="0 0 12 12"><rect x="1" y="2.5" width="10" height="7" fill="none" stroke="#fff" stroke-width="1.2"/><path d="M1 2.5l5 4 5-4" fill="none" stroke="#fff" stroke-width="1.2"/></svg></span><span>Shinefoxautocare@mailvento.com</span></li>
      <li><span class="icon"><svg viewBox="0 0 12 12"><circle cx="6" cy="6" r="4.5" fill="none" stroke="#fff" stroke-width="1.1"/><ellipse cx="6" cy="6" rx="2" ry="4.5" fill="none" stroke="#fff" stroke-width="1"/><path d="M1.5 6h9" stroke="#fff" stroke-width="1"/></svg></span><span>www.<span class="accent">Shinefoxautocare</span>.com</span></li>
      <li><span class="icon"><svg viewBox="0 0 12 12"><circle cx="6" cy="6" r="3" fill="none" stroke="#fff" stroke-width="1.3"/></svg></span><span>Shinefoxautocare</span></li>
      <li class="gap"><span class="icon"><svg viewBox="0 0 12 12"><path d="M6 11s-3.5-3.8-3.5-6.3a3.5 3.5 0 017 0C9.5 7.2 6 11 6 11z" fill="#fff"/><circle cx="6" cy="4.7" r="1.3" fill="#9b1010"/></svg></span><span>Merridale, Sk</span></li>
    </ul>
  </div>
</section>

</body>
</html>
```